Business card por a urban DJ, up scale audience target

Need a sober design, modern, conservative colors but i can consider some options, y play rnb, hip hop, EDM and top40.

Business card for contact and personal info, double sided, use logo attrached please; im 42 so i need a card acording to my age an target audience.

Target Market(s)

Adult people, up scale audience

Industry/Entity Type

Music Download

Contact Information for Business Card

Cel (318) 4207265518 www.lumadrift.com

Requirements
Must have
• open mind
Nice to have
• open mind
Should not have
• DJ

```html
<!DOCTYPE html>
<html lang="en">
<head>
<meta charset="utf-8">
<title>Luma business card</title>
<link rel="stylesheet" href="https://fonts.googleapis.com/css2?family=Open+Sans:wght@400;600&display=swap">
<style>
  :root {
    --ink: #2b2a29;
    --paper: #ffffff;
    --backdrop: #ece9e4;
  }
  * { margin: 0; padding: 0; box-sizing: border-box; }
  html, body {
    width: 1189px; height: 1200px; overflow: hidden;
    background: var(--backdrop);
    font-family: "Open Sans", Verdana, sans-serif;
  }
  .card {
    position: absolute; left: 171px; width: 856px; height: 488px;
    background: var(--ink); overflow: hidden;
    box-shadow: 4px 6px 10px rgba(0,0,0,0.25);
  }
  .card--front { top: 67px; }
  .card--back { top: 627px; }

  .front__panel {
    position: absolute; left: 0; top: 0; width: 411px; height: 100%;
    background: var(--paper);
  }
  .front__rule {
    position: absolute; left: 413px; top: 0; width: 4px; height: 100%;
    background: var(--paper);
  }

  .brand {
    position: absolute; display: flex; align-items: center; gap: 16px;
    font-weight: 600; font-size: 84px; letter-spacing: 4px; line-height: 1;
  }
  .brand__square { width: 40px; height: 40px; }
  .brand--dark { color: var(--ink); left: 0; width: 411px; top: 200px; justify-content: center; }
  .brand--dark .brand__square { background: var(--ink); }
  .brand--light { color: var(--paper); left: 0; width: 856px; top: 145px; justify-content: center; }
  .brand--light .brand__square { background: var(--paper); }

  .identity { position: absolute; left: 455px; top: 104px; color: var(--paper); }
  .identity__name { font-size: 31px; font-weight: 400; line-height: 1.1; letter-spacing: 0.3px; }
  .identity__role { font-size: 21px; line-height: 1.1; }

  .contact { position: absolute; left: 456px; top: 292px; list-style: none; color: var(--paper); }
  .contact__item {
    display: flex; align-items: center; gap: 8px;
    font-size: 23px; height: 30px;
  }
  .contact__icon { width: 22px; height: 22px; flex: none; }

  .back__url {
    position: absolute; left: 0; width: 856px; top: 416px;
    text-align: center; color: var(--paper); font-size: 21px;
  }
</style>
</head>
<body>

<section class="card card--front">
  <div class="front__panel">
    <div class="brand brand--dark"><span class="brand__square"></span>LUMA</div>
  </div>
  <div class="front__rule"></div>

  <div class="identity">
    <h1 class="identity__name">EMPLOYEE NAME</h1>
    <p class="identity__role">Development Manager</p>
  </div>

  <ul class="contact">
    <li class="contact__item">
      <svg class="contact__icon" viewBox="0 0 22 22" aria-hidden="true">
        <rect width="22" height="22" fill="#fff"/>
        <rect x="7" y="3" width="8" height="16" rx="1" fill="none" stroke="#2b2a29" stroke-width="1.6"/>
        <rect x="8.5" y="5" width="5" height="5" fill="#2b2a29"/>
      </svg>
      (318) 4207265518
    </li>
    <li class="contact__item">
      <svg class="contact__icon" viewBox="0 0 22 22" aria-hidden="true">
        <rect width="22" height="22" fill="#fff"/>
        <rect x="3.5" y="6" width="15" height="10" fill="none" stroke="#2b2a29" stroke-width="1.6"/>
        <path d="M3.5 6 L11 12 L18.5 6 M3.5 16 L9 11 M18.5 16 L13 11" fill="none" stroke="#2b2a29" stroke-width="1.4"/>
      </svg>
      hello@lumadrift.com
    </li>
    <li class="contact__item">
      <svg class="contact__icon" viewBox="0 0 22 22" aria-hidden="true">
        <rect width="22" height="22" fill="#fff"/>
        <circle cx="11" cy="11" r="7" fill="none" stroke="#2b2a29" stroke-width="1.4"/>
        <ellipse cx="11" cy="11" rx="3" ry="7" fill="none" stroke="#2b2a29" stroke-width="1.2"/>
        <path d="M4 11 H18 M5 7.5 H17 M5 14.5 H17" stroke="#2b2a29" stroke-width="1.1"/>
      </svg>
      www.lumadrift.com
    </li>
  </ul>
</section>

<section class="card card--back">
  <div class="brand brand--light"><span class="brand__square"></span>LUMA</div>
  <p class="back__url">www.lumadrift.com</p>
</section>

</body>
</html>
```